Stationery Design Task - Stationary, memo and report templates for professional services company

Looking for someone to update stationary design but just as importantly come up with a template for reports and memos for use in our consulting firm. Would also like some brand use guidelines to be able to share with our whole team. We have an existing logo that we like. Need to update with a more contemporary look so that our deliverables to clients look good and professional yet stylish. This is for business to business communications. No need for envelope design. Important to have design for multiple pages, i.e. first page of a report and then 2nd page. Need to use in MS word documents so must be easy to use and replicate. Don't want something overly complex. Clean, fresh looking is best.

Industry/Entity Type

Information Technology

Font styles to use
Sans Serif

Colors
33a6d7
0792cd
85cae6
cee9f5
cedeed
85abd2
3377b5
0455a3

Requirements
Must have
• Clean look but with a little style or pop. Something that can easily be used in word documents. Need to have page styles that have a first page of a report (not a cover page) and then secondary page.
Nice to have
• - Although the dark blue is our primary color. Might be willing to look at some accent color as well.
Should not have
• Not just our logo on the page with a color bar.

```html
<!DOCTYPE html>
<html lang="en">
<head>
<meta charset="utf-8">
<title>Crestline Systems – Letterhead Templates</title>
<link rel="stylesheet" href="https://fonts.googleapis.com/css2?family=Source+Sans+3:ital,wght@0,400;0,700;1,400&display=swap">
<style>
  :root {
    --backdrop: #cfcfcf;
    --headline: #17706b;
    --paper: #f8f8f8;
    --brand-dark: #0455a3;
    --brand-mid: #0792cd;
    --brand-blue: #3377b5;
    --brand-sky: #33a6d7;
    --brand-cyan: #16e0f0;
    --brand-mist: #cee9f5;
    --watermark: #e4e4e4;
  }
  * { box-sizing: border-box; margin: 0; padding: 0; }
  html, body { width: 1200px; height: 710px; overflow: hidden; }
  body {
    background: var(--backdrop);
    font-family: "Source Sans 3", "Helvetica Neue", Arial, sans-serif;
    position: relative;
  }
  .headline {
    position: absolute;
    top: 14px; left: 0; width: 1200px;
    text-align: center;
    font-style: italic;
    font-weight: 400;
    font-size: 52px;
    color: var(--headline);
    letter-spacing: 0.5px;
  }
  .sheet-row {
    position: absolute;
    top: 112px; left: 50px;
    display: flex; gap: 40px;
  }
  .sheet {
    position: relative;
    width: 340px; height: 481px;
    background: var(--paper);
    box-shadow: 0 14px 22px rgba(0,0,0,0.18);
    overflow: hidden;
  }
  .sheet__band {
    position: absolute; top: 0; left: 0; right: 0;
    height: 46px;
    background: linear-gradient(100deg, var(--brand-cyan) 0%, var(--brand-sky) 40%, var(--brand-mid) 70%, var(--brand-dark) 100%);
  }
  .sheet__tab {
    position: absolute; top: 30px; right: 92px;
    width: 142px; height: 44px;
    background: var(--paper);
    border-radius: 6px 6px 0 0;
    display: flex; align-items: center; justify-content: center; gap: 7px;
  }
  .brand__dot {
    width: 18px; height: 18px; border-radius: 50%;
    background: var(--brand-mid);
    flex: none;
  }
  .brand__name {
    color: var(--brand-mid);
    font-weight: 700;
    line-height: 1;
  }
  .brand__name-main { display: block; font-size: 17px; letter-spacing: -0.3px; }
  .brand__name-sub { display: block; font-size: 7px; letter-spacing: 3.4px; margin-top: 2px; }
  .sheet__watermark {
    position: absolute; left: 48px; top: 270px;
    width: 200px; height: 190px;
    border-radius: 50%;
    background: radial-gradient(circle at 50% 50%, var(--watermark) 0%, rgba(228,228,228,0.6) 55%, rgba(228,228,228,0) 72%);
  }
  .sheet__footer {
    position: absolute; left: 0; right: 0; bottom: 0;
    height: 24px;
    padding: 0 8px;
    background: linear-gradient(100deg, var(--brand-dark) 0%, var(--brand-mid) 55%, var(--brand-cyan) 100%);
    display: flex; align-items: center; justify-content: space-between;
    color: #ffffff;
    font-size: 5.2px;
    font-weight: 400;
  }
  .contact { display: flex; align-items: center; gap: 2px; white-space: nowrap; }
  .contact svg { width: 6px; height: 6px; flex: none; }
  .sheet__rule {
    position: absolute; left: 0; right: 0; bottom: 0;
    height: 6px;
    background: linear-gradient(90deg, var(--brand-dark) 0%, var(--brand-mid) 50%, var(--brand-cyan) 100%);
  }
</style>
</head>
<body>
  <h1 class="headline">Easy to use in Word Format</h1>

  <main class="sheet-row">
    <!-- First page -->
    <section class="sheet sheet--first">
      <div class="sheet__band"></div>
      <div class="sheet__tab">
        <span class="brand__dot"></span>
        <span class="brand__name"><span class="brand__name-main">CRESTLINE</span><span class="brand__name-sub">SYSTEMS</span></span>
      </div>
      <div class="sheet__watermark" role="img" aria-label="Faint large brand emblem watermark"></div>
      <footer class="sheet__footer">
        <span class="contact">
          <svg viewBox="0 0 10 10"><circle cx="5" cy="4" r="3" fill="none" stroke="#fff" stroke-width="1.4"/><path d="M5 10 L2.5 6 H7.5 Z" fill="#fff"/></svg>
          12 Harbour Lane, Westbrook, NZ41207
        </span>
        <span class="contact">
          <svg viewBox="0 0 10 10"><rect x="2.5" y="0.5" width="5" height="9" rx="1" fill="none" stroke="#fff" stroke-width="1.2"/></svg>
          (000) 555 0142
        </span>
        <span class="contact">
          <svg viewBox="0 0 10 10"><rect x="0.7" y="2" width="8.6" height="6" fill="none" stroke="#fff" stroke-width="1.1"/><path d="M0.7 2 L5 5.6 L9.3 2" fill="none" stroke="#fff" stroke-width="1.1"/></svg>
          hello@crestlinesystems.com
        </span>
        <span class="contact">
          <svg viewBox="0 0 10 10"><circle cx="5" cy="5" r="4.2" fill="none" stroke="#fff" stroke-width="1.1"/><path d="M0.8 5 H9.2 M5 0.8 V9.2" stroke="#fff" stroke-width="0.9"/></svg>
          www.crestlinesystems.com
        </span>
      </footer>
    </section>

    <!-- Continuation page -->
    <section class="sheet sheet--continuation">
      <div class="sheet__band"></div>
      <div class="sheet__tab">
        <span class="brand__dot"></span>
        <span class="brand__name"><span class="brand__name-main">CRESTLINE</span><span class="brand__name-sub">SYSTEMS</span></span>
      </div>
      <div class="sheet__watermark" role="img" aria-label="Faint large brand emblem watermark"></div>
      <div class="sheet__rule"></div>
    </section>

    <!-- Continuation page -->
    <section class="sheet sheet--continuation">
      <div class="sheet__band"></div>
      <div class="sheet__tab">
        <span class="brand__dot"></span>
        <span class="brand__name"><span class="brand__name-main">CRESTLINE</span><span class="brand__name-sub">SYSTEMS</span></span>
      </div>
      <div class="sheet__watermark" role="img" aria-label="Faint large brand emblem watermark"></div>
      <div class="sheet__rule"></div>
    </section>
  </main>
</body>
</html>
```